Mastering Modern Vineyard Management

size of the ad - 8”x 10.75" plus 0.25" bleed
I would like an ad for a magazine that will stand out and make people want to read the ad.
The ad should not be crowded and people reading the ad will be able to read the text.
I would like it to be a creative and modern-day design.
the list of topics should not be the focus of the ad.
the text is attached.
If you decide to use people in the ad then please no ladies.
please note that leave over 1 inch for the bottom of the footer

```html
<!DOCTYPE html>
<html lang="en">
<head>
<meta charset="utf-8">
<title>Course Ad</title>
<link href="https://fonts.googleapis.com/css2?family=Poppins:ital,wght@0,400;0,500;0,600;0,700;0,800;0,900;1,700&family=Oswald:wght@600&display=swap" rel="stylesheet">
<style>
  :root {
    --navy: #13283f;
    --cyan: #1497c0;
    --yellow: #e2f01c;
    --ink: #1c2430;
    --sky: #93cfdd;
    --paper: #ffffff;
    --backdrop: #e9eaec;
  }
  * { margin: 0; padding: 0; box-sizing: border-box; }
  html, body {
    width: 1200px; height: 2925px; overflow: hidden;
    background: var(--backdrop);
    font-family: "Poppins", sans-serif;
  }
  .ad-page {
    position: absolute; left: 102px; top: 800px;
    width: 995px; height: 1325px;
    background: var(--paper);
    box-shadow: 0 10px 40px rgba(0,0,0,0.25);
  }
  .ad-page > * { position: absolute; }
  .title { left: 64px; top: 70px; color: var(--navy); font-weight: 800; white-space: nowrap; }
  .title span { display: block; }
  .title-real { font-size: 140px; line-height: 120px; letter-spacing: -4px; }
  .title-estate { font-size: 96px; line-height: 86px; letter-spacing: -2px; }
  .title-course { font-size: 96px; line-height: 86px; letter-spacing: -2px; color: var(--cyan); }
  .subtitle {
    left: 66px; top: 385px; width: 430px;
    color: var(--ink); font-weight: 700; font-size: 40px; line-height: 48px;
    text-transform: uppercase;
  }
  .hero-art { left: 482px; top: 42px; width: 454px; height: 460px; }
  .slogan {
    left: 66px; top: 546px; width: 865px; height: 170px;
    background: var(--navy); border-radius: 48px;
    padding: 25px 0 0 32px;
    font-weight: 800; font-size: 50px; line-height: 60px; letter-spacing: -0.5px;
    color: #fff; text-transform: uppercase; white-space: nowrap;
  }
  .slogan span { display: block; }
  .slogan .accent { color: var(--yellow); }
  .city { left: 64px; top: 740px; color: var(--cyan); font-weight: 900; font-size: 78px; line-height: 1; letter-spacing: -1px; }
  .schedule { left: 66px; top: 830px; color: var(--ink); font-weight: 700; font-size: 43px; line-height: 42px; text-transform: uppercase; }
  .start-badge {
    left: 66px; top: 918px; width: 432px; height: 70px;
    border: 3px solid var(--cyan); border-radius: 14px; overflow: hidden;
    display: flex; align-items: center; background: #fff;
  }
  .start-badge .label { width: 165px; text-align: center; font-weight: 700; font-size: 28px; color: var(--ink); }
  .start-badge .date {
    flex: 1; height: 100%; background: var(--navy); border-radius: 12px;
    color: #fff; font-family: "Oswald", sans-serif; font-weight: 600; font-size: 46px;
    display: flex; align-items: center; justify-content: center; letter-spacing: -0.5px;
  }
  .start-badge .date .yellow { color: var(--yellow); }
  .start-badge sup { font-size: 22px; margin-right: 8px; position: relative; top: -6px; }
  .scholarship { left: 66px; top: 1004px; font-weight: 700; font-size: 25px; color: var(--ink); text-transform: uppercase; }
  .early-bird { left: 66px; top: 1040px; font-weight: 800; font-size: 34px; color: var(--cyan); text-transform: uppercase; }
  .audience { left: 66px; top: 1088px; width: 440px; font-weight: 500; font-size: 27px; line-height: 31px; color: var(--ink); }
  .topics { left: 550px; top: 744px; }
  .topics h2 { font-weight: 700; font-size: 25px; color: var(--navy); text-transform: uppercase; margin-bottom: 10px; }
  .topics ul { list-style: none; }
  .topics li { display: flex; align-items: center; gap: 12px; height: 39px; padding-left: 4px; font-size: 18px; color: #333; }
  .topics svg { flex: none; }
</style>
</head>
<body>
  <main class="ad-page">
    <h1 class="title">
      <span class="title-real">REAL</span>
      <span class="title-estate">ESTATE</span>
      <span class="title-course">COURSE</span>
    </h1>
    <p class="subtitle">Mastering<br>Modern Vineyard<br>Management</p>

    <svg class="hero-art" viewBox="0 0 454 460" role="img" aria-label="Illustration of a presenter beside property listings, a key, a calculator and stacked coins">
      <path d="M240 8 C360 0 454 90 440 220 C430 330 400 440 270 452 C150 462 30 420 10 300 C-8 190 40 110 110 60 C150 30 190 12 240 8 Z" fill="var(--sky)"/>
    </svg>

    <p class="slogan"><span>Investing in knowledge is</span><span class="accent">investing in opportunities.</span></p>

    <p class="city">LARKFIELD</p>
    <p class="schedule">10 -Tuesday<br>Evenings Sessions</p>
    <div class="start-badge">
      <span class="label">STARTING</span>
      <span class="date"><span class="yellow">28</span><sup class="yellow">TH</sup>FEBRUARY</span>
    </div>
    <p class="scholarship">Limited Partial Scholarships</p>
    <p class="early-bird">Early Bird Special</p>
    <p class="audience">For those that started or would like to go into real estate</p>

    <section class="topics">
      <h2>Topics: Partial Listing</h2>
      <ul>
        <li><svg width="13" height="13" viewBox="0 0 14 14"><circle cx="7" cy="7" r="6" fill="none" stroke="#444" stroke-width="1.3"/><path d="M4 7.2l2 2 4-4" fill="none" stroke="#444" stroke-width="1.3"/></svg>Real estate investment strategies</li>
        <li><svg width="13" height="13" viewBox="0 0 14 14"><circle cx="7" cy="7" r="6" fill="none" stroke="#444" stroke-width="1.3"/><path d="M4 7.2l2 2 4-4" fill="none" stroke="#444" stroke-width="1.3"/></svg>Due diligence</li>
        <li><svg width="13" height="13" viewBox="0 0 14 14"><circle cx="7" cy="7" r="6" fill="none" stroke="#444" stroke-width="1.3"/><path d="M4 7.2l2 2 4-4" fill="none" stroke="#444" stroke-width="1.3"/></svg>Financing</li>
        <li><svg width="13" height="13" viewBox="0 0 14 14"><circle cx="7" cy="7" r="6" fill="none" stroke="#444" stroke-width="1.3"/><path d="M4 7.2l2 2 4-4" fill="none" stroke="#444" stroke-width="1.3"/></svg>Underwriting</li>
        <li><svg width="13" height="13" viewBox="0 0 14 14"><circle cx="7" cy="7" r="6" fill="none" stroke="#444" stroke-width="1.3"/><path d="M4 7.2l2 2 4-4" fill="none" stroke="#444" stroke-width="1.3"/></svg>Property management</li>
        <li><svg width="13" height="13" viewBox="0 0 14 14"><circle cx="7" cy="7" r="6" fill="none" stroke="#444" stroke-width="1.3"/><path d="M4 7.2l2 2 4-4" fill="none" stroke="#444" stroke-width="1.3"/></svg>Real estate Legal basics</li>
        <li><svg width="13" height="13" viewBox="0 0 14 14"><circle cx="7" cy="7" r="6" fill="none" stroke="#444" stroke-width="1.3"/><path d="M4 7.2l2 2 4-4" fill="none" stroke="#444" stroke-width="1.3"/></svg>Sourcing deals</li>
        <li><svg width="13" height="13" viewBox="0 0 14 14"><circle cx="7" cy="7" r="6" fill="none" stroke="#444" stroke-width="1.3"/><path d="M4 7.2l2 2 4-4" fill="none" stroke="#444" stroke-width="1.3"/></svg>Syndication</li>
        <li><svg width="13" height="13" viewBox="0 0 14 14"><circle cx="7" cy="7" r="6" fill="none" stroke="#444" stroke-width="1.3"/><path d="M4 7.2l2 2 4-4" fill="none" stroke="#444" stroke-width="1.3"/></svg>Dealing with brokers</li>
        <li><svg width="13" height="13" viewBox="0 0 14 14"><circle cx="7" cy="7" r="6" fill="none" stroke="#444" stroke-width="1.3"/><path d="M4 7.2l2 2 4-4" fill="none" stroke="#444" stroke-width="1.3"/></svg>Tax fundamentals</li>
      </ul>
    </section>
  </main>
</body>
</html>
```